Cat-products company needs smart, yet endearing, business card

We need a business card design for a new, but up-and-running, business based in Honolulu, Hawaii. The business is Purrnest Nook Co. Our first product is the most environmentally-friendly cat grass kit ever seen on the planet. Future products, currently in the R&D phase, will include a variety of exciting cat scratchers. We also do consulting work to help apartment-dwellers make their home more cat-friendly and, in the future, plan on doing full, custom installs of structure to create high walkways for cats.

Target Market(s)

Middle-aged, apartment-dwelling, middle-class workers who own 1 or more cats and who dote on them.

Industry/Entity Type

Pet Care

Contact Information for Business Card

A striking, professional, yet warm and friendly design is what we're after.

Font styles to use
Serif
Sans Serif
Other font styles liked:
• Comfortaa

Colors

Designer to choose colors to be used in the design.

Requirements
Must have
• The company logo: (see attachment)
• The company name: Purrnest Nook Co
• The web address: www.purrnestnookco.com
• Email: support@purrnestnookco.com
• Phone: +1 (808) 571 6023
• Update (Fri Jun 30 3017 7:45pm Hawaii Time) I would like, is possible, uploaded picture of the cat grass kit on the back of the card with some text along the lines of: Purrnest Nook Co - Maker Of The Leafiest Feline Sprout Set Yet
Nice to have
• A cat picture, cartoon, real or silhouette that illustrates cats in action and/or relaxing; ie using the apartment space to live, play and relax in and being well-contented.
• Most of the website is done in the font: Comfortaa. It might be nice to continue using this for brand consistency.
Should not have
• Hard-to-read fonts.

```html
<!DOCTYPE html>
<html lang="en">
<head>
<meta charset="utf-8">
<title>Purrnest Nook Co – Business Card</title>
<link href="https://fonts.googleapis.com/css2?family=Open+Sans:wght@400;600;700&display=swap" rel="stylesheet">
<style>
  :root {
    --backdrop: #3b3430;
    --card: #0e0d0d;
    --gold: #f7b500;
    --brown: #5b3b33;
    --text-light: #e9e6e2;
    --text-soft: #cfcac4;
  }
  * { margin: 0; padding: 0; box-sizing: border-box; }
  html, body {
    width: 1200px; height: 900px; overflow: hidden;
    background: var(--backdrop);
    font-family: "Open Sans", Arial, sans-serif;
  }
  .canvas { position: relative; width: 1200px; height: 900px; }

  .card {
    position: absolute;
    width: 525px; height: 300px;
    background: var(--card);
    border-radius: 3px;
    box-shadow: 0 18px 40px rgba(0,0,0,0.45);
  }
  .card--contact { left: 60px; top: 390px; }
  .card--brand { left: 615px; top: 210px; }

  .brand-square { width: 20px; height: 20px; background: var(--brown); flex: none; }
  .brand-name {
    font-weight: 700; color: var(--gold);
    white-space: nowrap; line-height: 1;
  }

  /* contact side */
  .contact-brand {
    position: absolute; left: 28px; top: 138px;
    display: flex; align-items: center; gap: 10px;
  }
  .contact-brand .brand-name { font-size: 22px; }

  .divider {
    position: absolute; left: 270px; top: 70px;
    width: 1px; height: 130px;
    background: linear-gradient(to bottom, transparent, var(--gold) 30%, var(--gold) 70%, transparent);
  }
  .person { position: absolute; left: 300px; top: 82px; }
  .person-name {
    font-weight: 600; font-size: 17px; letter-spacing: 0.5px;
    color: var(--gold); text-transform: uppercase;
  }
  .person-title { font-size: 12px; color: var(--text-soft); margin-top: 2px; }

  .contact-list { position: absolute; left: 300px; top: 158px; list-style: none; }
  .contact-item {
    display: flex; align-items: center; gap: 8px;
    font-size: 13px; color: var(--text-light); line-height: 20px;
    white-space: nowrap;
  }
  .contact-icon { width: 11px; height: 11px; flex: none; }

  /* brand side */
  .brand-lockup {
    position: absolute; inset: 0;
    display: flex; align-items: center; justify-content: center; gap: 16px;
  }
  .brand-lockup .brand-square { width: 32px; height: 32px; }
  .brand-lockup .brand-name { font-size: 36px; }
</style>
</head>
<body>
<main class="canvas">

  <section class="card card--contact" aria-label="Business card, contact side">
    <div class="contact-brand">
      <span class="brand-square"></span>
      <span class="brand-name">Purrnest Nook Co</span>
    </div>
    <div class="divider"></div>
    <div class="person">
      <p class="person-name">Malia Kealoha</p>
      <p class="person-title">Managing Director</p>
    </div>
    <ul class="contact-list">
      <li class="contact-item">
        <svg class="contact-icon" viewBox="0 0 24 24"><path fill="#f7b500" d="M6.6 10.8a15.1 15.1 0 0 0 6.6 6.6l2.2-2.2c.3-.3.7-.4 1-.2 1.1.4 2.3.6 3.6.6.6 0 1 .4 1 1V20c0 .6-.4 1-1 1A17 17 0 0 1 3 4c0-.6.4-1 1-1h3.5c.6 0 1 .4 1 1 0 1.3.2 2.5.6 3.6.1.3 0 .7-.2 1z"/></svg>
        <span>+1 (808) 571 6023</span>
      </li>
      <li class="contact-item">
        <svg class="contact-icon" viewBox="0 0 24 24"><rect x="2" y="5" width="20" height="14" rx="1" fill="#f7b500"/><path d="M2 6l10 7 10-7" fill="none" stroke="#0e0d0d" stroke-width="2"/></svg>
        <span>support@purrnestnookco.com</span>
      </li>
      <li class="contact-item">
        <svg class="contact-icon" viewBox="0 0 24 24"><circle cx="12" cy="12" r="10" fill="#f7b500"/><path d="M2 12h20M12 2c3 3 3 17 0 20M12 2c-3 3-3 17 0 20" fill="none" stroke="#0e0d0d" stroke-width="1.5"/></svg>
        <span>www.purrnestnookco.com</span>
      </li>
    </ul>
  </section>

  <section class="card card--brand" aria-label="Business card, brand side">
    <div class="brand-lockup">
      <span class="brand-square"></span>
      <span class="brand-name">Purrnest Nook Co</span>
    </div>
  </section>

</main>
</body>
</html>
```